UK landscaping company needs website

We, Brackwell Landscapes need a website design for a company based in Surrey, UK. The design should be bold and playful. We have three main areas of work driveways, paving and fencing. It shouldn't be too heavy in text and concentrate on the pictures from previous jobs we've completed. You may use stock images for the design, these can be changed if you are successful. Please don’t just copy the flyer it is just there to provide content.
We have a logo design which we would also like editing slightly.
Here are some of my local competitors
https://www.pelmarlandscapes.example.co.uk/

https://www.twinfirgardendesign.example.com/

https://kestbyrnlandscapes.example.co.uk/

Industry/Entity Type

Landscaping

Coding

Coded - Design and coding required

Number of Pages Required

3 page

Font styles to use
Sans Serif

Requirements
Must have
• Pictures of my previous jobs.
Must be mobile friendly
Easy to navigate
Nice to have
• Try to use different colours. It would be good to have some designs that aren’t just black and green.
I’d like some curves in the design.
Should not have
• We install hard landscaping. Think more building/construction and less plants and cutting grass.

```html
<!DOCTYPE html>
<html lang="en">
<head>
<meta charset="utf-8">
<title>Brackwell Landscapes</title>
<link href="https://fonts.googleapis.com/css2?family=Poppins:wght@300;400;600;700;800&family=Roboto:wght@400;500;700&display=swap" rel="stylesheet">
<style>
:root{
  --green:#5cb731;
  --green-dark:#3f9a1c;
  --black:#000;
  --ink:#111;
  --muted:#777;
  --white:#fff;
  --light:#eceeed;
}
*{box-sizing:border-box;margin:0;padding:0}
html,body{width:1200px;height:3521px;overflow:hidden}
body{position:relative;background:var(--white);font-family:"Roboto",Arial,sans-serif;color:var(--ink)}
.abs{position:absolute}
.btn{position:absolute;display:flex;align-items:center;justify-content:center;gap:6px;background:var(--green);color:var(--white);border-radius:30px;font:700 14px "Roboto",Arial,sans-serif;text-transform:uppercase;letter-spacing:.2px}
.btn svg{width:13px;height:13px}
.heading{font-family:"Poppins",Arial,sans-serif;font-weight:700;color:var(--black);text-transform:uppercase;letter-spacing:-.5px}
.heading span{color:var(--green);font-weight:400}

/* header */
.site-header{left:0;top:0;width:1200px;height:123px;background:var(--black)}
.brand{left:112px;top:30px;color:var(--white);font:700 30px/1 "Poppins",Arial,sans-serif;letter-spacing:.5px}
.brand small{display:block;font-size:13px;letter-spacing:3px;margin-top:6px}
.nav a{position:absolute;top:50px;color:var(--white);font:700 14px "Roboto",Arial,sans-serif;text-decoration:none}
.nav a.active{color:var(--green)}
.divider{left:926px;top:30px;width:1px;height:66px;background:#666}
.phone-dot{left:949px;top:41px;width:40px;height:40px;border-radius:50%;background:var(--green);display:flex;align-items:center;justify-content:center}
.call{left:999px;top:40px;color:var(--white);font:700 16px "Roboto",Arial,sans-serif}
.call strong{display:block;font-size:23px;margin-top:2px}

/* hero */
.hero-photo{left:0;top:123px;width:1200px;height:680px;background:linear-gradient(180deg,#6f8fb8 0%,#b9c3cf 35%,#9a8f7c 70%,#5c6a4a 100%)}
.hero-box{left:167px;top:291px;width:866px;height:267px;background:rgba(140,140,140,.72);text-align:center;color:var(--white)}
.hero-box h1{margin-top:30px;font:800 56px/1.2 "Poppins",Arial,sans-serif;text-shadow:3px 3px 0 rgba(0,0,0,.45)}
.hero-box p{width:760px;margin:14px auto 0;font-size:14.5px;line-height:26px}
.slider-dots{left:570px;top:615px;display:flex;gap:8px;align-items:center}
.slider-dots i{width:13px;height:13px;border:2px solid #111;border-radius:50%}
.slider-dots i.on{width:17px;height:17px;border-color:var(--green)}

/* about */
.about-corner{left:142px;top:1055px;width:130px;height:129px;background:var(--green);clip-path:polygon(0 0,14% 0,14% 86%,100% 86%,86% 100%,0 100%)}
.about-photo{left:160px;top:816px;width:388px;height:351px;background:linear-gradient(160deg,#8a5a48 0%,#b7a285 40%,#cfcfcd 70%,#4f7a3a 100%);border-radius:4px}
.about-title{left:597px;top:806px;font-size:41px;line-height:43px}
.about-text{left:597px;top:899px;width:495px;font-size:14px;line-height:25.7px;color:var(--muted)}

/* services */
.services{left:0;top:1278px;width:1200px;height:633px;background:linear-gradient(180deg,#e6e8e8,#f0f1f1 60%,#e9eaea)}
.services-title{left:0;top:1345px;width:1200px;text-align:center;font-size:38px}
.service{position:absolute;top:1412px;width:300px;text-align:center}
.service .ring{width:282px;height:282px;margin:0 auto;border-radius:50%;border:5px solid var(--green);overflow:hidden}
.service .ring div{width:100%;height:100%}
.service h3{margin-top:14px;font:600 23px "Poppins",Arial,sans-serif;color:var(--black)}
.service svg{display:block;margin:4px auto 0}
.service p{margin-top:6px;font-size:14.5px;line-height:26px;color:var(--muted)}

/* gallery */
.gallery-title{left:0;top:1994px;width:1200px;text-align:center;font-size:39px}
.tile{position:absolute;width:311px;height:240px;border-radius:4px}
.tile.feature{background:var(--green);display:flex;align-items:center;justify-content:center}
.diamond{width:20px;height:20px;background:var(--green);transform:rotate(45deg)}

/* contact */
.contact-band{left:0;top:2680px;width:1200px;height:640px}
.contact-title{left:0;top:2826px;width:1200px;text-align:center;font:700 38px "Poppins",Arial,sans-serif;color:var(--white)}
.field{position:absolute;background:var(--white);border:1px solid #cfcfcf;padding:0 18px;font-size:14px;color:#999;display:flex;align-items:center}
.field.area{align-items:flex-start;padding-top:18px}
.remember{left:355px;top:3180px;color:var(--white);font-size:14px;display:flex;align-items:center;gap:6px}
.remember i{width:11px;height:11px;border:1px solid var(--white)}
.submit{left:515px;top:3160px;width:170px;height:54px;background:var(--black);color:var(--white);border-radius:30px;font:700 15px "Roboto",Arial,sans-serif;letter-spacing:2px;display:flex;align-items:center;justify-content:center}
.verify{left:714px;top:3160px;width:201px;height:54px;background:#f9f9f9;border:1px solid #d3d3d3;display:flex;align-items:center;padding:0 12px;gap:8px;font-size:9px;color:#222}
.verify .box{width:18px;height:18px;border:2px solid #c1c1c1;background:var(--white)}
.verify .mark{margin-left:auto;text-align:center;font-size:6px;color:#777;line-height:9px}
.verify .mark b{display:block;width:20px;height:20px;margin:0 auto 1px;background:#c9d4e8}

/* footer */
.socials{left:0;top:3352px;width:1200px;display:flex;justify-content:center;gap:10px}
.socials i{width:37px;height:37px;border:2px solid #222;border-radius:50%;position:relative}
.socials i::after{content:"";position:absolute;inset:7px;border:1.5px solid #222;border-radius:50%}
.footer-nav{left:0;top:3411px;width:1200px;text-align:center;font-size:14px;color:#333;word-spacing:2px}
.footer-nav span{margin:0 15px}
.copy{left:0;top:3456px;width:1200px;text-align:center;font-size:14px;color:#333}
</style>
</head>
<body>

<header class="abs site-header">
  <div class="abs brand">BRACKWELL<small>LANDSCAPES</small></div>
  <nav class="nav">
    <a class="active" style="left:369px">Home</a>
    <a style="left:446px">Services</a>
    <a style="left:542px">Commercial Contracts</a>
    <a style="left:725px">Work Gallery</a>
    <a style="left:845px">Contact</a>
  </nav>
  <svg class="abs" style="left:366px;top:70px" width="48" height="10" viewBox="0 0 48 10"><path d="M2 8 Q24 -2 46 4 Q24 2 2 8Z" fill="var(--green)"/></svg>
  <div class="abs divider"></div>
  <div class="abs phone-dot"><svg width="16" height="16" viewBox="0 0 24 24"><path fill="#fff" d="M6.6 10.8a15 15 0 006.6 6.6l2.2-2.2c.3-.3.7-.4 1-.2 1.1.4 2.3.6 3.6.6.6 0 1 .4 1 1V20c0 .6-.4 1-1 1A17 17 0 013 4c0-.6.4-1 1-1h3.5c.6 0 1 .4 1 1 0 1.3.2 2.5.6 3.6.1.3 0 .7-.2 1z"/></svg></div>
  <div class="abs call">Call us Today :<strong>+1 888 888 8888</strong></div>
</header>

<section>
  <div class="abs hero-photo" role="img" aria-label="Construction site with cranes and high-rise buildings under a cloudy sky"></div>
  <div class="abs hero-box">
    <h1>BRACKWELL LANDSCAPES</h1>
    <p>Lorem ipsum dolor sit amet, consectetur adipiscing elit, sed do eiusmod tempor incididunt ut labore et dolore magna aliqua. Ut enim ad minim veniam, quis nostrud exercitation</p>
  </div>
  <a class="btn" style="left:514px;top:469px;width:174px;height:46px">Learn more <svg viewBox="0 0 16 16"><circle cx="8" cy="8" r="8" fill="#fff"/><path d="M6 4l4 4-4 4" stroke="var(--green)" stroke-width="2" fill="none"/></svg></a>
  <div class="abs slider-dots"><i></i><i class="on"></i><i></i></div>
  <svg class="abs" style="left:0;top:640px" width="1200" height="170" viewBox="0 0 1200 170">
    <path d="M0 148 Q600 -40 1200 148 L1200 170 L0 170Z" fill="var(--green)"/>
    <path d="M0 160 Q600 0 1200 155 L1200 170 L0 170Z" fill="var(--white)"/>
  </svg>
</section>

<section>
  <div class="abs about-corner"></div>
  <div class="abs about-photo" role="img" aria-label="Timber pergola over a pale stone patio beside a brick wall and lawn"></div>
  <h2 class="abs heading about-title">About <span>Brackwell<br>Landscapes</span></h2>
  <p class="abs about-text">Sed ut perspiciatis unde omnis iste natus error sit voluptatem accusantium doloremque laudantium, totam rem aperiam, eaque ipsa quae ab illo inventore veritatis et quasi architecto beatae vitae dicta sunt explicabo. Nemo enim ipsam voluptatem quia voluptas sit aspernatur aut odit aut fugit, sed quia consequuntur magni dolores eos qui ratione voluptatem sequi nesciunt. Neque porro quisquam est, qui dolorem ipsum quia dolor Sed ut perspiciatis unde omnis iste natus error sit voluptatem accusantium doloremque laudantium, totam rem aperiam, eaque ipsa quae ab illo inventore veritatis et quasi</p>
  <a class="btn" style="left:597px;top:1121px;width:175px;height:46px">Learn more <svg viewBox="0 0 16 16"><circle cx="8" cy="8" r="8" fill="#fff"/><path d="M6 4l4 4-4 4" stroke="var(--green)" stroke-width="2" fill="none"/></svg></a>
</section>

<section>
  <div class="abs services" role="img" aria-label="Faded background of a paved patio"></div>
  <h2 class="abs heading services-title">Our <span>Services</span></h2>
  <div class="service" style="left:97px">
    <div class="ring"><div role="img" aria-label="Swimming pool surrounded by sandstone paving" style="background:linear-gradient(180deg,#4a5a48 0%,#3fb6df 30%,#c7a58a 55%,#a58c78 100%)"></div></div>
    <h3>Driveways</h3>
    <svg width="56" height="10" viewBox="0 0 56 10"><path d="M2 9 Q28 -3 54 5 Q28 2 2 9Z" fill="var(--green)"/></svg>
    <p>Nemo enim ipsam voluptatem quia voluptas sit aspernatur aut odit aut fugit, sed quia consequuntur magni</p>
  </div>
  <div class="service" style="left:446px">
    <div class="ring"><div role="img" aria-label="Raised lawn with timber sleeper steps and fence panels" style="background:linear-gradient(180deg,#d9dde0 0%,#6b5646 20%,#5a9a38 55%,#8a5a34 80%,#3a3430 100%)"></div></div>
    <h3>Paving</h3>
    <svg width="56" height="10" viewBox="0 0 56 10"><path d="M2 9 Q28 -3 54 5 Q28 2 2 9Z" fill="var(--green)"/></svg>
    <p>Nemo enim ipsam voluptatem quia voluptas sit aspernatur aut odit aut fugit, sed quia consequuntur magni</p>
  </div>
  <div class="service" style="left:796px">
    <div class="ring"><div role="img" aria-label="New timber fence with gravel border and lawn" style="background:linear-gradient(180deg,#7c9a6a 0%,#9c7a52 25%,#8a6844 65%,#4c7a2e 100%)"></div></div>
    <h3>Fencing</h3>
    <svg width="56" height="10" viewBox="0 0 56 10"><path d="M2 9 Q28 -3 54 5 Q28 2 2 9Z" fill="var(--green)"/></svg>
    <p>Nemo enim ipsam voluptatem quia voluptas sit aspernatur aut odit aut fugit, sed quia consequuntur magni</p>
  </div>
</section>

<section>
  <h2 class="abs heading gallery-title">Project <span>Gallery</span></h2>
  <div class="tile" style="left:111px;top:2068px;background:linear-gradient(170deg,#5c7ab0,#b89c74 45%,#6a5a4e)" role="img" aria-label="Timber pergola over a patio with garden furniture"></div>
  <div class="tile feature" style="left:444px;top:2068px" role="img" aria-label="Lawn mower on grass under a green overlay"><svg width="40" height="40" viewBox="0 0 40 40"><circle cx="20" cy="20" r="16" fill="none" stroke="#fff" stroke-width="3"/></svg></div>
  <div class="tile" style="left:778px;top:2068px;background:linear-gradient(150deg,#6c6c6a,#8a8a88 50%,#b8b6b0)" role="img" aria-label="Grey block paved path curving past a house"></div>
  <div class="tile" style="left:111px;top:2328px;background:linear-gradient(170deg,#8a4a36,#cfcfcc 35%,#b7b7b3 75%,#b07c50)" role="img" aria-label="Wide grey porcelain patio steps"></div>
  <div class="tile" style="left:444px;top:2328px;background:linear-gradient(170deg,#8a4a36,#a45a40 35%,#4f8a32 60%,#cdcdca)" role="img" aria-label="Brick house with lawn and pale patio"></div>
  <div class="tile" style="left:778px;top:2328px;background:linear-gradient(170deg,#c8aa74,#d6b684 35%,#3e6a2a 65%,#8a6a40)" role="img" aria-label="Timber decking with sleeper-edged lawn"></div>
  <div class="abs diamond" style="left:422px;top:2308px"></div>
  <div class="abs diamond" style="left:757px;top:2308px"></div>
  <a class="btn" style="left:513px;top:2595px;width:174px;height:46px">View more <svg viewBox="0 0 16 16"><circle cx="8" cy="8" r="8" fill="#fff"/><path d="M6 4l4 4-4 4" stroke="var(--green)" stroke-width="2" fill="none"/></svg></a>
</section>

<section>
  <svg class="abs contact-band" viewBox="0 0 1200 640" role="img" aria-label="Green tinted block paving">
    <defs><linearGradient id="paving" x1="0" y1="0" x2="1" y2="1"><stop offset="0" stop-color="#5cb731"/><stop offset=".6" stop-color="#52ad2a"/><stop offset="1" stop-color="#63bd38"/></linearGradient></defs>
    <path d="M68 163 Q600 -85 1148 130 Q600 -30 68 163Z" fill="var(--black)"/>
    <path d="M0 150 Q600 -50 1200 150 L1200 640 L0 640Z" fill="url(#paving)"/>
  </svg>
  <h2 class="abs contact-title">CONTACT US</h2>
  <div class="field" style="left:261px;top:2904px;width:331px;height:52px">First name*</div>
  <div class="field" style="left:606px;top:2904px;width:331px;height:52px">Last name*</div>
  <div class="field" style="left:261px;top:2973px;width:331px;height:52px">Phone*</div>
  <div class="field" style="left:606px;top:2973px;width:331px;height:52px">Email Address*</div>
  <div class="field area" style="left:261px;top:3042px;width:676px;height:104px">Name*</div>
  <div class="abs remember"><i></i>Forget password</div>
  <div class="abs submit">SUBMIT</div>
  <div class="abs verify"><span class="box"></span>I'm not a robot<span class="mark"><b></b>VerifyGate<br>Privacy · Terms</span></div>
</section>

<footer>
  <div class="abs socials"><i aria-label="Social link"></i><i aria-label="Social link"></i><i aria-label="Social link"></i><i aria-label="Social link"></i></div>
  <div class="abs footer-nav">HOME<span>/</span>SERVICES<span>/</span>COMMERCIAL CONTRACTS<span>/</span>WORK GALLERY<span>/</span>CONTACT</div>
  <div class="abs copy">© Copyrights 2020 Company name | All Rights Reserved</div>
</footer>

</body>
</html>
```